Web Design Project

Looking for an eye catching banner page to be used on the website and LinkedIn. We are an Executive Recruiting and HR Consulting service firm with a modern edge. We want to demonstrate through our brand that we are using the latest recruiting trends to find talent and that we are easy to work with- innovative and simple.We typically recruit for Engineers, IT professionals, Accounting and Operation Managers. Our website is www.bluvantatalent.com and it needs a fresh clean look. We love our logo but might want to use the "8" to show the 2 sides of our business or maybe to use the infinity concept or continuous improvement. We like the Green and white colors with accents in gray.

Target Market(s)

Small to mid-sized Business Managers seeking innovation

Industry/Entity Type

Business

Requirements
Must have
• Use of the 8
Long picture on top to be used on LinkedIn and the website top
Clean Simple look- modern font like century gothic
Nice to have
• Smiling face(s)
Layered image of 8 or of photo stock faces
Maybe a modern office so they feel that they walked in to meet us (fyi our office has white chandeliers and green walls that match our logo)
Should not have
• Busy or cluttered feel

```html
<!DOCTYPE html>
<html lang="en">
<head>
<meta charset="utf-8">
<title>Bluvanta — Where strategy meets recruiting</title>
<link href="https://fonts.googleapis.com/css2?family=Questrial&family=Arimo:wght@400;700&display=swap" rel="stylesheet">
<style>
:root{
  --green:#a9b500;
  --green-dark:#939d00;
  --orange:#e07a1f;
  --slate:#5d6470;
  --nav:#343b47;
  --footer:#3a414e;
  --footer-deep:#323844;
  --ink:#2b2b2b;
  --text:#8a8a8a;
  --rule:#e6e6e6;
  --white:#ffffff;
}
*{box-sizing:border-box;margin:0;padding:0}
html,body{width:1064px;height:1200px;overflow:hidden;background:var(--white)}
body{font-family:"Arimo",Arial,sans-serif;color:var(--text);position:relative}
.page{position:relative;width:1064px;height:1200px;border-top:4px solid var(--green);border-bottom:4px solid var(--green)}
.wrap{position:absolute;left:166px;width:732px}

/* header */
.header{position:absolute;top:0;left:0;width:100%;height:62px}
.brand{position:absolute;left:166px;top:13px;font-family:"Questrial",sans-serif;font-size:30px;color:var(--green);letter-spacing:1px}
.audience{position:absolute;right:166px;top:28px;display:flex;gap:3px}
.audience a{display:block;width:93px;height:22px;line-height:22px;text-align:center;color:var(--white);font-family:"Questrial",sans-serif;font-size:11px;text-decoration:none}
.audience .candidates{background:var(--slate)}
.audience .clients{background:var(--green)}

/* nav */
.nav{position:absolute;top:62px;left:0;width:100%;height:36px;background:var(--nav)}
.nav ul{list-style:none;position:absolute;left:166px;width:732px;top:0;height:36px;display:flex;justify-content:space-between;align-items:center}
.nav li{font-size:11px;color:#e4e6ea;display:flex;align-items:center}
.nav li.active{color:var(--green)}
.nav .sep{color:#6c7380;font-size:14px}

/* hero */
.hero{position:absolute;top:98px;left:0;width:100%;height:343px;
  background:linear-gradient(90deg,#e9ecef 0%,#cfd3d6 25%,#c2bfb8 45%,#d7d3cd 60%,#8c8f97 80%,#a7b0b8 100%)}
.hero h1{position:absolute;left:166px;top:32px;font-family:"Questrial",sans-serif;font-weight:400;font-size:30px;color:#333}

/* services */
.services{top:478px;height:200px}
.service{position:absolute;top:0;width:240px;text-align:center}
.service .badge{width:72px;height:72px;margin:0 auto;border-radius:50%;border:2px solid var(--green);padding:3px}
.service .badge span{display:flex;align-items:center;justify-content:center;width:100%;height:100%;border-radius:50%;background:var(--green)}
.service h2{margin-top:18px;font-family:"Questrial",sans-serif;font-weight:400;font-size:12.5px;color:var(--green);letter-spacing:.3px}
.service p{margin-top:12px;font-size:9px;line-height:12.6px;color:var(--text)}
.s1{left:-10px}.s2{left:247px}.s3{left:502px}
.flow{position:absolute;top:34px}
.f1{left:170px}.f2{left:272px}.f3{left:427px}.f4{left:528px}
.divider{position:absolute;top:672px;left:166px}

/* lower sections */
.section-title{font-family:"Questrial",sans-serif;font-weight:400;font-size:12.5px;color:var(--green);letter-spacing:.3px}
.expertise{top:736px;width:306px}
.expertise ul{list-style:none;margin-top:18px}
.expertise li{height:17px;line-height:16px;font-size:9px;letter-spacing:.6px;color:#8d8d8d;border-bottom:1px dotted #dedede;padding-left:20px;position:relative}
.expertise li::before{content:"";position:absolute;left:2px;top:5px;width:4px;height:4px;border-right:1px solid #bbb;border-bottom:1px solid #bbb;transform:rotate(-45deg)}
.vrule{position:absolute;left:532px;top:740px;width:1px;height:180px;background:#ececec}
.testimonials{top:736px;left:567px;width:331px}
.quote{margin-top:14px}
.quote p{font-size:9px;line-height:12.6px;color:#8a8a8a}
.quote cite{display:block;margin-top:3px;font-style:normal;font-size:9px;color:var(--ink)}
.testimonials .quote:first-of-type{margin-top:18px}

/* footer */
.footer{position:absolute;top:956px;left:0;width:100%;height:177px;background:var(--footer)}
.footer h3{font-family:"Questrial",sans-serif;font-weight:400;font-size:12.5px;color:var(--white);letter-spacing:.4px}
.fcol{position:absolute;top:18px}
.useful{left:166px}.quick{left:463px}.contact{left:740px}
.btn{display:flex;justify-content:space-between;align-items:center;width:118px;height:19px;margin-top:6px;padding:0 8px;color:var(--white);font-size:9px}
.btn:first-of-type{margin-top:14px}
.btn.find{background:var(--orange)}.btn.ats{background:var(--green)}.btn.apply{background:var(--slate)}
.fdiv{position:absolute;top:48px;width:1px;height:108px;border-left:1px dashed #59606c}
.fdiv.a{left:360px}.fdiv.b{left:678px}
.quick ul{list-style:none;margin-top:14px}
.quick li{font-size:8.5px;color:#aeb3bb;line-height:16.8px;letter-spacing:.3px}
.quick li::before{content:"›";color:var(--green);margin-right:8px;font-size:10px}
.contact ul{list-style:none;margin-top:14px}
.contact li{font-size:8.5px;color:#aeb3bb;line-height:16.8px;padding-left:22px;position:relative;letter-spacing:.3px}
.contact li.name{color:var(--green)}
.contact svg{position:absolute;left:0;top:4px}
.bottom{position:absolute;top:1133px;left:0;width:100%;height:63px;background:var(--footer-deep)}
.legal{position:absolute;left:166px;top:18px;font-size:8.5px;line-height:16px;color:#aeb3bb}
.legal b{font-family:"Questrial",sans-serif;font-weight:400;color:var(--green);font-size:9px}
.social{position:absolute;right:166px;top:19px;display:flex;gap:4px}
.social span{width:23px;height:23px;border-radius:50%;background:#9a9ea6}
</style>
</head>
<body>
<div class="page">

  <header class="header">
    <div class="brand">BLUVANTA</div>
    <nav class="audience">
      <a class="candidates" href="#">CANDIDATES</a>
      <a class="clients" href="#">CLIENTS</a>
    </nav>
  </header>

  <nav class="nav">
    <ul>
      <li class="active">Home</li><li class="sep">/</li>
      <li>Recruiting Services</li><li class="sep">/</li>
      <li>HR Consulting Services</li><li class="sep">/</li>
      <li>Testimonials</li><li class="sep">/</li>
      <li>Job Openings</li><li class="sep">/</li>
      <li>Job Application</li><li class="sep">/</li>
      <li>Contact Us</li>
    </ul>
  </nav>

  <section class="hero" role="img" aria-label="Photo of smiling business professionals standing in front of a city office building">
    <h1>Where strategy meets recruiting</h1>
  </section>

  <section class="wrap services">
    <div class="service s1">
      <div class="badge"><span>
        <svg width="30" height="30" viewBox="0 0 30 30" fill="none" stroke="#fff" stroke-width="2.4"><circle cx="13" cy="13" r="7"/><path d="M18 18l7 7" stroke-linecap="round"/></svg>
      </span></div>
      <h2>RECRUITING</h2>
      <p>Bluvanta combines strategy and action to find high-impact hires in the areas of Engineering, IT/Technology, Operations, Executive Leadership, Accounting and Administration. We bring creative solutions to complex searches where other search firms have been unsuccessful.</p>
    </div>
    <svg class="flow f1" width="40" height="8" viewBox="0 0 40 8"><path d="M0 4h33" stroke="#d8d8d8" stroke-dasharray="3 2"/><path d="M33 1l4 3-4 3z" fill="#d8d8d8"/></svg>
    <svg class="flow f2" width="36" height="8" viewBox="0 0 36 8"><path d="M0 4h34" stroke="#e4e4e4" stroke-dasharray="3 2"/></svg>
    <div class="service s2">
      <div class="badge"><span>
        <svg width="30" height="30" viewBox="0 0 30 30" fill="none" stroke="#fff" stroke-width="2.4"><circle cx="10" cy="10" r="5"/><path d="M13.5 13.5L24 24M20 20l3-3M17 17l2.5-2.5" stroke-linecap="round"/></svg>
      </span></div>
      <h2>HUMAN RESOURCE CONSULTING</h2>
      <p>Our PHR/SPHR certified professional HR consultants partner with you to co-create sound HR processes and solutions to people challenges. Our solutions are always keeping in mind the most important asset of any organization...<br>it's employees!</p>
    </div>
    <svg class="flow f3" width="40" height="8" viewBox="0 0 40 8"><path d="M0 4h33" stroke="#d8d8d8" stroke-dasharray="3 2"/><path d="M33 1l4 3-4 3z" fill="#d8d8d8"/></svg>
    <svg class="flow f4" width="36" height="8" viewBox="0 0 36 8"><path d="M0 4h34" stroke="#e4e4e4" stroke-dasharray="3 2"/></svg>
    <div class="service s3">
      <div class="badge"><span>
        <svg width="30" height="30" viewBox="0 0 30 30" fill="#fff"><rect x="5" y="5" width="9" height="9"/><rect x="16" y="5" width="9" height="9"/><rect x="5" y="16" width="9" height="9"/><rect x="16" y="16" width="9" height="9" opacity=".7"/></svg>
      </span></div>
      <h2>RECRUITING TURNKEY CONSULTING</h2>
      <p>Our scalable recruiting solutions provide you with an on-demand recruiting department at your fingertips for 1 to multiple hires. Our highly experienced team creates solutions are tailored to your needs from tapping into new candidate pools, screening resumes, interviewing, staff interview training,</p>
    </div>
  </section>

  <svg class="divider" width="732" height="50" viewBox="0 0 732 50" fill="none" stroke="#ececec" stroke-width="1.2">
    <path d="M2 4 Q2 22 24 22 H330 Q362 22 366 48 Q370 22 402 22 H708 Q730 22 730 4"/>
  </svg>

  <section class="wrap expertise">
    <h2 class="section-title">RECRUITING AREAS OF EXPERTISE</h2>
    <ul>
      <li>ADMINISTRATIVE</li>
      <li>ACCOUNTING</li>
      <li>ENGINEERING</li>
      <li>OPERATIONS</li>
      <li>MARKETING</li>
      <li>SALES</li>
      <li>HUMAN RESOURCES</li>
      <li>TECHNOLOGY</li>
      <li style="border-bottom:none">MEDICAL</li>
    </ul>
  </section>

  <div class="vrule"></div>

  <section class="wrap testimonials">
    <h2 class="section-title">TESTIMONIALS</h2>
    <blockquote class="quote">
      <p>"Bluvanta has been very attentive to the needs of our Corporation. From providing administrative to technical candidates, they operate in a professional manner and will go above and beyond to achieve exceptional results."</p>
      <cite>Orbital Contract Company</cite>
    </blockquote>
    <blockquote class="quote">
      <p>"Bluvanta delivered a depth of experience that we had never encountered in a recruiting agency, including a detailed understanding of our business needs and innovative solutions to help us achieve our goals."</p>
      <cite>Technical Writing Firm</cite>
    </blockquote>
    <blockquote class="quote">
      <p>"What differentiates Bluvanta from other HR service firms is their desire to find the right HR solutions for your unique company culture."</p>
      <cite>Architecture Firm</cite>
    </blockquote>
  </section>

  <footer class="footer">
    <div class="fcol useful">
      <h3>USEFULL LINKS</h3>
      <div class="btn find"><span>Find Job</span><span>›</span></div>
      <div class="btn ats"><span>Welcom to ATS</span><span>›</span></div>
      <div class="btn apply"><span>Apply Now</span><span>›</span></div>
    </div>
    <div class="fdiv a"></div>
    <div class="fcol quick">
      <h3>QUICK LINKS</h3>
      <ul>
        <li>Home</li>
        <li>Recruiting Services</li>
        <li>HR Consulting Services</li>
        <li>Testimonials</li>
        <li>Job Openings</li>
        <li>Job Application</li>
        <li>Contact Us</li>
      </ul>
    </div>
    <div class="fdiv b"></div>
    <div class="fcol contact">
      <h3>CONTACT US</h3>
      <ul>
        <li class="name">Bluvanta</li>
        <li><svg width="10" height="13" viewBox="0 0 10 13"><path d="M5 0a4.5 4.5 0 0 0-4.5 4.5C.5 8 5 13 5 13s4.5-5 4.5-8.5A4.5 4.5 0 0 0 5 0z" fill="#a9b500"/><circle cx="5" cy="4.5" r="1.7" fill="#3a414e"/></svg>1400 Meridian Park Dr</li>
        <li>Suite 210 Austin TX 78701</li>
        <li><svg width="12" height="9" viewBox="0 0 12 9"><path d="M1 3c3-3 7-3 10 0L9.5 4.5 8 3H4L2.5 4.5z M3 5h6v4H3z" fill="#a9b500"/></svg>512.555.0142</li>
        <li><svg width="8" height="11" viewBox="0 0 8 11"><rect x="0.5" y="0.5" width="7" height="10" rx="1" fill="none" stroke="#a9b500"/><rect x="2" y="2" width="4" height="6" fill="#a9b500"/></svg>512.555.0187</li>
        <li><svg width="12" height="9" viewBox="0 0 12 9"><path d="M1 3c3-3 7-3 10 0L9.5 4.5 8 3H4L2.5 4.5z" fill="#a9b500"/><rect x="4" y="5" width="4" height="4" fill="#a9b500"/></svg>512.555.0163</li>
        <li><svg width="12" height="8" viewBox="0 0 12 8"><rect width="12" height="8" fill="#a9b500"/><path d="M0 0l6 4.5L12 0" stroke="#3a414e" fill="none"/></svg>www.bluvantatalent.com</li>
      </ul>
    </div>
  </footer>

  <div class="bottom">
    <div class="legal">info@bluvantatalent.com<br>Copyright © 2013 <b>BLUVANTA</b></div>
    <div class="social" aria-label="Social links">
      <span></span><span></span><span></span><span></span><span></span><span></span>
    </div>
  </div>

</div>
</body>
</html>
```